Brightway Haus Inc. Business Card Design

Brightway Haus Inc. is in search of a great clean design for our business cards!

Looking to incorporate our full logo and watermark on side one (however, I am open to having the text and watermark separated within the design.)

On side two, I am looking to have contact information (Name, Position, Phone #, Email, Website (www.thebrightwayhaus.ca). Can have the logo and/or watermark as part of the design if applicable.

Please add tagline "Where Shine Counts" on either side 1 or 2. This tagline can be in a sans serif, serif or cursive font as long as it compliments overall design. Capitalization can be title or sentence case depending on how it fits within the design.

Get creative!! Looking for a clean, crisp, premium design! Looking for a glossy card finish with spot UV features when printed. Cards will also be printed with rounded corners. Standard dimensions (3.5 x 2).

Target Market(s)

B2B - primary clients are business owners or property management corporations. (residential jobs are few and far between)

Industry/Entity Type

Business

Contact Information for Business Card

- clean, crisp design
- double sided
- spot UV accents and glossy finish upon printing
- standard business card size (3.5 x 2) with rounded corners
- please see project description for requirements per side

Font styles to use
Sans Serif

Requirements
Must have
• - adequate bleeds with print ready files
• - cohesive design elements between side 1 & 2
• - spot UV elements (can be on both sides or just one, use your discretion)
• - colour pallet should match the logo file provided
• - incorporate tagline "where shine counts" (this tagline can be in a serif or sans serif font as long as it is complimentary to the overall design.
Nice to have
• - Premium elements with a clean design
Should not have
• - Please omit cartoon or whimsical like designs, think premium.
• - Colours should not stray from the pallet of the provided logo.

```html
<!DOCTYPE html>
<html lang="en">
<head>
<meta charset="utf-8">
<title>Brightway Haus Inc. Business Card</title>
<link href="https://fonts.googleapis.com/css2?family=Roboto:ital,wght@0,400;0,500;0,700;1,400&family=Roboto+Condensed:wght@500;700&display=swap" rel="stylesheet">
<style>
  :root {
    --teal: #13b8bb;
    --navy: #1b2451;
    --paper: #f3f3f3;
    --text: #4a4a4a;
    --stage: #2b2b2b;
  }
  html, body {
    margin: 0;
    width: 1200px;
    height: 960px;
    overflow: hidden;
    background: var(--stage);
    font-family: "Roboto", Arial, sans-serif;
  }
  .card {
    position: absolute;
    width: 600px;
    height: 343px;
    overflow: hidden;
  }
  .card-front { left: 314px; top: 113px; background: var(--paper); }
  .card-back  { left: 311px; top: 472px; background: var(--navy); }

  .accent-bar {
    position: absolute;
    top: 0;
    right: 0;
    width: 44px;
    height: 100%;
    background: var(--teal);
  }
  .base-band {
    position: absolute;
    left: 0;
    right: 0;
    bottom: 0;
    height: 14px;
    background: var(--navy);
  }

  .brand-name {
    position: absolute;
    left: 44px;
    top: 58px;
    display: flex;
    align-items: center;
    gap: 10px;
    font-family: "Roboto Condensed", "Arial Narrow", sans-serif;
    font-weight: 700;
    font-size: 27px;
    letter-spacing: 0.2px;
    color: var(--navy);
  }
  .brand-square { width: 22px; height: 22px; background: var(--teal); }

  .address {
    position: absolute;
    left: 45px;
    top: 161px;
    margin: 0;
    font-size: 14.5px;
    line-height: 18px;
    color: var(--text);
    font-style: normal;
  }
  .contact-list {
    position: absolute;
    left: 43px;
    top: 211px;
    margin: 0;
    padding: 0;
    list-style: none;
    font-size: 14.5px;
    line-height: 19px;
    color: var(--text);
  }
  .contact-list li { display: flex; align-items: center; gap: 8px; }
  .contact-list svg { width: 13px; height: 13px; fill: var(--teal); flex: none; }

  .person {
    position: absolute;
    left: 392px;
    top: 168px;
    width: 156px;
    text-align: center;
  }
  .person-name {
    margin: 0;
    font-family: "Roboto Condensed", "Arial Narrow", sans-serif;
    font-weight: 700;
    font-size: 21px;
    color: var(--teal);
  }
  .person-role {
    margin: 2px 0 0;
    font-family: "Roboto Condensed", "Arial Narrow", sans-serif;
    font-weight: 500;
    font-size: 14.5px;
    color: var(--navy);
  }

  .back-brand {
    position: absolute;
    left: 0;
    right: 0;
    top: 132px;
    display: flex;
    justify-content: center;
    align-items: center;
    gap: 14px;
    font-family: "Roboto Condensed", "Arial Narrow", sans-serif;
    font-weight: 700;
    font-size: 34px;
    color: #ffffff;
  }
  .back-square { width: 30px; height: 30px; background: #ffffff; }

  .tagline {
    position: absolute;
    left: 0;
    right: 0;
    top: 280px;
    display: flex;
    justify-content: center;
    align-items: center;
    gap: 6px;
    font-style: italic;
    font-size: 19px;
    color: #ffffff;
  }
  .tagline-rule { width: 115px; height: 1px; }
  .tagline-rule.left  { background: linear-gradient(to right, rgba(255,255,255,0), #ffffff); }
  .tagline-rule.right { background: linear-gradient(to left, rgba(255,255,255,0), #ffffff); }
</style>
</head>
<body>

<section class="card card-front" aria-label="Card front">
  <span class="accent-bar"></span>
  <span class="base-band"></span>

  <div class="brand-name"><span class="brand-square"></span>BRIGHTWAY HAUS INC.</div>

  <address class="address">2140 Lakeview Crescent<br>Halton Hills, Ontario L7G 4S2</address>

  <ul class="contact-list">
    <li><svg viewBox="0 0 16 16"><path d="M3.5 1l3 3-1.6 2a9 9 0 0 0 5.1 5.1l2-1.6 3 3-1.8 2.2C7 14.5 1.5 9 .8 3z"/></svg>905 555 0148</li>
    <li><svg viewBox="0 0 16 16"><path d="M4 0h8a1 1 0 0 1 1 1v14a1 1 0 0 1-1 1H4a1 1 0 0 1-1-1V1a1 1 0 0 1 1-1zm1 2v10h6V2zm3 11a1 1 0 1 0 0 2 1 1 0 0 0 0-2z"/></svg>905 555 0193</li>
    <li><svg viewBox="0 0 16 16"><path d="M4 0h8v4H4zM1 5h14v7h-3v4H4v-4H1zm4 5v5h6v-5z"/></svg>905 555 0176</li>
    <li><svg viewBox="0 0 16 16"><path d="M0 3h16v10H0zm1.5 1.2L8 9l6.5-4.8V4h-13z"/></svg>mara@brightwayhaus.ca</li>
    <li><svg viewBox="0 0 16 16"><path d="M8 0a8 8 0 1 0 0 16A8 8 0 0 0 8 0zm0 1.5a6.5 6.5 0 0 1 4.6 1.9L11 5 9 4 7 6l2 2-1 3-3-3-2.7 1A6.5 6.5 0 0 1 8 1.5z"/></svg>www.thebrightwayhaus.ca</li>
  </ul>

  <div class="person">
    <p class="person-name">MARA KELLAND</p>
    <p class="person-role">CEO/FOUNDER</p>
  </div>
</section>

<section class="card card-back" aria-label="Card back">
  <div class="back-brand"><span class="back-square"></span>BRIGHTWAY HAUS INC.</div>
  <div class="tagline">
    <span class="tagline-rule left"></span>
    <span>Where Shine Counts</span>
    <span class="tagline-rule right"></span>
  </div>
</section>

</body>
</html>
```